Website Re-design and extension of an existing website

I have a Wordpress website currently and I need it to be upgraded. I have MOST of the content to get it started and the rest (video's, pictures ect) are on the way. I want to know if it is possible to convert my existing website into a Personal Brand website with a public speaking emphasis. I would like to have my website modeled after the following website:

http://www.vokalmira.com/

I have attached a document entitled "Website Outline & Content" that has all of the text on it and it has red headlines that indicate where something needs to be added or designed. I will be happy to give more detail if needed.

Things I still need to get to you in order to design the website;

-Demo video
-Full length public speaking video

Target Market(s)

Corporations, universities, trade associations, private events

Coding

Coded - Design and coding required

Requirements
Must have
• Pictures, links, downloadable forms, MULTIPLE video's embedded, my logo, keep the colors in sync with my existing marketing material
Nice to have
• I would like my design colors thematic as already inherent in my marketing materials (see my Speaker One Sheet)

```html
<!DOCTYPE html>
<html lang="en">
<head>
<meta charset="utf-8">
<title>Tobin Arkwright – Holistic Lifestyle Speaker</title>
<link href="https://fonts.googleapis.com/css2?family=Oswald:wght@400;500;600&family=Roboto:wght@300;400;500;700&display=swap" rel="stylesheet">
<style>
:root{
  --olive:#8a8b48;
  --olive-light:#a3a35c;
  --olive-dark:#4d5026;
  --footer:#565a2d;
  --footer-deep:#454823;
  --ink:#2b2b2b;
  --muted:#666;
  --grey-band:#e6e6e6;
  --white:#fff;
}
*{box-sizing:border-box;margin:0;padding:0}
html,body{width:1200px;height:3020px;overflow:hidden}
body{font-family:'Roboto',sans-serif;color:var(--ink);background:var(--white);position:relative}
.wrap{width:1040px;margin:0 auto;position:relative}

/* header */
.site-header{height:88px;background:var(--white)}
.site-header .wrap{height:88px;display:flex;align-items:center;justify-content:space-between}
.brand{display:flex;align-items:center;gap:12px}
.brand-mark{width:46px;height:46px;border-radius:50%;background:var(--olive)}
.brand-name{font-family:'Oswald',sans-serif;font-weight:600;font-size:30px;color:var(--olive-dark);letter-spacing:1px}
.connect{display:flex;align-items:center;gap:10px;font-size:14px;color:var(--ink)}
.social-dot{width:28px;height:28px;border-radius:50%;background:var(--olive-dark)}

/* nav */
.main-nav{height:32px;background:var(--olive)}
.main-nav ul{list-style:none;display:flex;justify-content:space-between;width:1040px;margin:0 auto;height:32px;align-items:center}
.main-nav a{color:var(--white);font-size:13px;text-decoration:none}

/* hero */
.hero{height:540px;position:relative;background:linear-gradient(90deg,#3d3d34 0%,#6f6a5b 40%,#8d8a74 70%,#5e5a48 100%)}
.hero-photo{position:absolute;inset:0;background:linear-gradient(180deg,rgba(190,200,215,.55) 0%,rgba(120,110,90,.2) 45%,rgba(40,38,30,.55) 100%)}
.hero-text{position:absolute;left:80px;top:140px;color:var(--white)}
.hero-text h1{font-family:'Oswald',sans-serif;font-weight:500;font-size:78px;letter-spacing:2px;line-height:1}
.hero-text p{font-size:26px;font-weight:300;line-height:1.35;margin-top:12px;width:560px}
.hero-btn{display:inline-block;margin-top:22px;border:2px solid var(--white);color:var(--white);font-size:15px;padding:10px 20px;line-height:1.3;text-align:center}

/* signup */
.signup{height:100px;background:var(--olive-dark);position:relative}
.book{position:absolute;left:160px;top:-70px;width:200px;height:240px;background:linear-gradient(135deg,#d9c988,#8b7c3e);box-shadow:4px 6px 12px rgba(0,0,0,.35)}
.signup-text{position:absolute;left:400px;top:24px;color:var(--white);font-family:'Oswald',sans-serif}
.signup-text strong{display:block;font-size:30px;font-weight:500;line-height:1}
.signup-text span{font-size:18px;letter-spacing:1px}
.signup-form{position:absolute;left:615px;top:30px;display:flex}
.signup-form .field{width:330px;height:40px;background:var(--white);font-size:14px;color:#999;padding:11px 14px}
.signup-form .btn{width:110px;height:40px;background:var(--olive);color:var(--white);font-size:14px;text-align:center;line-height:40px}

/* intro */
.intro{height:310px;text-align:center;padding-top:90px}
.intro h2{font-size:30px;font-weight:500;line-height:1.3}
.downloads{display:flex;justify-content:center;gap:36px;margin-top:40px}
.download-btn{width:300px;height:68px;background:var(--olive);color:var(--white);font-size:16px;display:flex;align-items:center;justify-content:center;line-height:1.3;padding:0 30px;box-shadow:0 3px 0 var(--olive-dark)}

/* sugar */
.sugar{height:470px;background:var(--grey-band);position:relative}
.portrait{position:absolute;left:140px;top:55px;width:360px;height:360px;border-radius:50%;border:12px solid var(--white);background:radial-gradient(circle at 50% 40%,#c8a48a,#6c7a8a 70%);box-shadow:0 4px 12px rgba(0,0,0,.15)}
.sugar-copy{position:absolute;left:565px;top:80px}
.sugar-copy h3{font-size:30px;font-weight:400;color:var(--olive-dark)}
.sugar-copy h4{font-size:24px;font-weight:400;margin-top:4px}
.sugar-copy ul{list-style:none;margin-top:22px}
.sugar-copy li{display:flex;align-items:center;gap:14px;font-size:20px;margin-bottom:20px}
.tick{width:28px;height:28px;flex:none}

/* video */
.video-section{height:400px;position:relative}
.video-copy{position:absolute;left:100px;top:60px;width:470px}
.video-copy h2{font-size:36px;font-weight:500}
.video-copy p{font-size:14px;color:var(--muted);line-height:1.6;margin-top:18px}
.learn-btn{display:inline-block;margin-top:22px;background:var(--olive-dark);color:var(--white);font-size:15px;padding:11px 28px}
.video-frame{position:absolute;left:640px;top:50px;width:430px;height:290px;background:linear-gradient(135deg,#8a8060,#3f3a2c)}
.play{position:absolute;left:185px;top:115px}

/* testimonials */
.testimonials{height:390px;background:var(--grey-band);text-align:center;padding-top:40px}
.testimonials h2{font-size:36px;font-weight:400}
.divider{margin:6px auto 0;display:block}
.quotes{display:flex;justify-content:center;gap:40px;margin-top:30px}
.quote{width:410px}
.quote-box{background:var(--white);border:1px solid #ccc;padding:40px 34px 30px;position:relative;font-size:13px;font-style:italic;color:var(--muted);line-height:1.6}
.quote-mark{position:absolute;left:50%;top:-18px;margin-left:-18px;width:36px;height:36px;border-radius:50%;background:var(--olive);color:var(--white);font-family:'Oswald',sans-serif;font-size:26px;line-height:40px;font-style:normal}
.author{display:flex;align-items:center;justify-content:center;gap:10px;margin-top:14px}
.avatar{width:50px;height:50px;border-radius:50%;background:linear-gradient(135deg,#c9a68c,#7b6a5a);border:3px solid var(--white)}
.author span{font-size:13px;color:var(--muted)}

/* clients */
.clients{height:250px;text-align:center;padding-top:36px}
.clients h2{font-size:36px;font-weight:400;color:var(--olive-dark)}
.client-row{display:flex;justify-content:space-between;width:1060px;margin:48px auto 0;align-items:center}
.client-name{font-size:28px;font-weight:500;color:#8c8c8c}

/* footer */
.site-footer{height:360px;background:var(--footer);color:var(--white);position:relative}
.footer-col{position:absolute;top:56px}
.footer-col h5{font-size:22px;font-weight:400;margin-bottom:22px}
.links{left:70px;display:grid;grid-template-columns:230px 160px;row-gap:10px}
.links h5{grid-column:1/3;margin-bottom:12px}
.links span{font-size:14px;opacity:.9}
.contact{left:520px}
.contact-row{display:flex;align-items:center;gap:10px;font-size:14px;margin-bottom:12px}
.newsletter{left:800px;width:340px}
.newsletter p{font-size:19px;line-height:1.4}
.newsletter .field{margin-top:24px;height:38px;background:var(--white);color:#999;font-size:14px;padding:10px 14px}
.newsletter .btn{margin-top:12px;width:130px;height:38px;background:var(--olive);text-align:center;line-height:38px;font-size:15px}
.copyright{position:absolute;left:0;right:0;bottom:0;height:40px;background:var(--footer-deep);text-align:center;font-size:12px;line-height:40px;opacity:.95}
</style>
</head>
<body>

<header class="site-header">
  <div class="wrap">
    <div class="brand"><div class="brand-mark"></div><span class="brand-name">TOBIN ARKWRIGHT</span></div>
    <div class="connect">Connect with Tobin Arkwright
      <span class="social-dot"></span><span class="social-dot"></span><span class="social-dot"></span><span class="social-dot"></span>
    </div>
  </div>
</header>

<nav class="main-nav">
  <ul>
    <li><a>Home</a></li><li><a>About Tobin Arkwright</a></li><li><a>Motivational Speaker/Keynotes</a></li>
    <li><a>Workshop Presenter</a></li><li><a>Author</a></li><li><a>Coaching</a></li><li><a>Blog</a></li>
    <li><a>Online Courses</a></li><li><a>Contact Tobin Arkwright</a></li>
  </ul>
</nav>

<section class="hero">
  <div class="hero-photo" role="img" aria-label="Photo of the speaker standing on a balcony with mountains behind"></div>
  <div class="hero-text">
    <h1>TOBIN ARKWRIGHT</h1>
    <p>Sugar Addiction Expert, Holistic Health Expert, Author &amp; Speaker</p>
    <span class="hero-btn">See How Tobin Arkwright Can Help You<br>or Your Organization</span>
  </div>
</section>

<section class="signup">
  <div class="book" role="img" aria-label="Cover of the speaker's latest book"></div>
  <div class="signup-text"><strong>SIGN UP FOR OUR</strong><span>LATEST BOOK NOW</span></div>
  <div class="signup-form"><div class="field">Email address</div><div class="btn">SUBSCRIBE</div></div>
</section>

<section class="intro">
  <h2>Your Holistic Lifestyle Hacker<br>Lose Your Mind &amp; Find Your Health!</h2>
  <div class="downloads">
    <div class="download-btn">Download Tobin's Speaker One Sheet</div>
    <div class="download-btn">Download Tobin's Media Sheet</div>
    <div class="download-btn">Download Tobin's College Speaker One Sheet</div>
  </div>
</section>

<section class="sugar">
  <div class="portrait" role="img" aria-label="Round portrait photo of the speaker"></div>
  <div class="sugar-copy">
    <h3>Sugar Addiction</h3>
    <h4>(The Stealth Addiction) is destroying:</h4>
    <ul>
      <li><svg class="tick" viewBox="0 0 28 28"><circle cx="14" cy="14" r="14" fill="#8a8b48"/><path d="M8 14.5l4 4 8-9" stroke="#fff" stroke-width="2.6" fill="none"/></svg>Your bottom-line</li>
      <li><svg class="tick" viewBox="0 0 28 28"><circle cx="14" cy="14" r="14" fill="#8a8b48"/><path d="M8 14.5l4 4 8-9" stroke="#fff" stroke-width="2.6" fill="none"/></svg>Your Insurance Premiums</li>
      <li><svg class="tick" viewBox="0 0 28 28"><circle cx="14" cy="14" r="14" fill="#8a8b48"/><path d="M8 14.5l4 4 8-9" stroke="#fff" stroke-width="2.6" fill="none"/></svg>The health of your employees</li>
      <li><svg class="tick" viewBox="0 0 28 28"><circle cx="14" cy="14" r="14" fill="#8a8b48"/><path d="M8 14.5l4 4 8-9" stroke="#fff" stroke-width="2.6" fill="none"/></svg>The culture of your company</li>
    </ul>
  </div>
</section>

<section class="video-section">
  <div class="video-copy">
    <h2>Watch Our Latest Video</h2>
    <p>For over 17 years, Tobin Arkwright has tirelessly helped executives, employees, and everyday people achieve lasting health and fitness by helping them "lose their minds." Using his unique Lifestyle Coaching System, speaking platform, and online training courses, Tobin has helped hundreds of people shed their limiting beliefs, eat better, shed sugar addiction and transform their bodies and minds.</p>
    <span class="learn-btn">Learn More</span>
  </div>
  <div class="video-frame" role="img" aria-label="Video still of the speaker outdoors">
    <svg class="play" width="60" height="60" viewBox="0 0 60 60"><circle cx="30" cy="30" r="30" fill="#fff"/><path d="M24 18l18 12-18 12z" fill="#2b2b2b"/></svg>
  </div>
</section>

<section class="testimonials">
  <h2>Testimonials</h2>
  <svg class="divider" width="140" height="14" viewBox="0 0 140 14"><line x1="0" y1="7" x2="58" y2="7" stroke="#999"/><circle cx="70" cy="7" r="5" fill="#8a8b48"/><line x1="82" y1="7" x2="140" y2="7" stroke="#999"/></svg>
  <div class="quotes">
    <div class="quote">
      <div class="quote-box"><span class="quote-mark">"</span>Tobin's keynote changed how our whole team eats and works. People still talk about it months later and our energy at work is higher than ever before.</div>
      <div class="author"><div class="avatar" role="img" aria-label="Small author photo"></div><span>By Author Name, City Location</span></div>
    </div>
    <div class="quote">
      <div class="quote-box"><span class="quote-mark">"</span>A practical, funny and honest speaker. Our staff left with clear steps to cut sugar and feel better, and many of them have kept going with his course.</div>
      <div class="author"><div class="avatar" role="img" aria-label="Small author photo"></div><span>By Author Name, City Location</span></div>
    </div>
  </div>
</section>

<section class="clients">
  <h2>Our Clients</h2>
  <div class="client-row">
    <span class="client-name">Stellan</span><span class="client-name">Mavenly</span><span class="client-name">Corvex</span>
    <span class="client-name">Lumora</span><span class="client-name">Tessly</span><span class="client-name">Brightal</span>
  </div>
</section>

<footer class="site-footer">
  <div class="footer-col links">
    <h5>Quick Links</h5>
    <span>Home</span><span>Coaching</span>
    <span>About Tobin Arkwright</span><span>Blog</span>
    <span>Motivational Speaker/Keynotes</span><span>Online Courses</span>
    <span>Workshop Presenter</span><span>Contact Tobin Arkwright</span>
    <span>Author</span><span></span>
  </div>
  <div class="footer-col contact">
    <h5>Contact Info</h5>
    <div class="contact-row"><svg width="16" height="16" viewBox="0 0 16 16"><path d="M8 1a5 5 0 0 0-5 5c0 4 5 9 5 9s5-5 5-9a5 5 0 0 0-5-5z" fill="#fff"/><circle cx="8" cy="6" r="2" fill="#565a2d"/></svg>1215 Ridgeline Ave, Suite 4</div>
    <div class="contact-row"><svg width="16" height="16" viewBox="0 0 16 16"><circle cx="8" cy="8" r="7" fill="#fff"/></svg>Cedar Falls, 54021</div>
    <div class="contact-row"><svg width="16" height="16" viewBox="0 0 16 16"><path d="M3 2l3 0 1 3-2 1.5a8 8 0 0 0 4 4L10.5 9l3 1v3a1 1 0 0 1-1 1A11 11 0 0 1 2 3a1 1 0 0 1 1-1z" fill="#fff"/></svg>555-019-2284</div>
    <div class="contact-row"><svg width="16" height="16" viewBox="0 0 16 16"><rect x="1" y="3" width="14" height="10" fill="#fff"/><path d="M1 3l7 6 7-6" stroke="#565a2d" fill="none"/></svg>hello@tobinarkwright.com</div>
  </div>
  <div class="footer-col newsletter">
    <p>Become a Holistic Health Hacker and receive a FREE 30-Day Meal Plan crafted by Tobin!</p>
    <div class="field">Email address</div>
    <div class="btn">Subscribe</div>
  </div>
  <div class="copyright">© 2017 Tobin Arkwright. All Rights Reserved.</div>
</footer>

</body>
</html>
```